Garlic Farm for Farm Sales/Restaurant sales

Need a professional, but appealing to agriculture world. We are selling 27 kinds of Organic Garlic from a farm in Simla,CO. I have uploaded logo and business information-we are going to need a template, because I will need to use it for four separate people.
-We are trying to appeal to Farm to table restaurants
-As well as growers/farmers

Target Market(s)

Agriculture Sales/Restaurants-Organic

Industry/Entity Type

Agriculture

Contact Information for Business Card

Want it to look more unique then your average kelto stock card- I want it to look amazing

Font styles to use
Sans Serif

Colors
0455a3
ec1f27
fbed22
ffffff

Requirements
Must have
• Just be creative
Nice to have
• Colorful
Should not have
• plain

```html
<!DOCTYPE html>
<html lang="en">
<head>
<meta charset="utf-8">
<title>Ridgeline Garlic – Business Card</title>
<link href="https://fonts.googleapis.com/css2?family=Open+Sans:wght@400;600&display=swap" rel="stylesheet">
<style>
  :root{
    --navy:#0b2c5c;
    --red:#d21f2f;
    --yellow:#f6d21c;
    --white:#ffffff;
    --ink:#4a4a4a;
    --rule:#2b2b2b;
    --backdrop:#e9e6e1;
    --glow:#fbf1e6;
  }
  *{box-sizing:border-box;margin:0;padding:0}
  html,body{width:1200px;height:987px;overflow:hidden}
  body{background:var(--backdrop);font-family:"Open Sans",Arial,sans-serif;position:relative}
  .card{position:absolute;left:292px;width:616px;height:352px;box-shadow:0 3px 8px rgba(0,0,0,.25);overflow:hidden}
  .card--front{top:130px;background:var(--white)}
  .card--back{top:506px;background:var(--navy)}

  .edge-stripe{position:absolute;left:0;top:0;width:11px;height:100%;background:var(--navy)}
  .edge-stripe::before{content:"";position:absolute;left:0;top:0;width:100%;height:95px;background:var(--red)}
  .edge-stripe::after{content:"";position:absolute;left:0;top:95px;width:100%;height:55px;background:var(--yellow)}

  .faint-mark{position:absolute;left:395px;top:55px;width:270px;height:270px;border-radius:50%;background:var(--glow)}

  .brand{position:absolute;left:42px;top:58px;display:flex;align-items:center;gap:12px}
  .brand__dot{width:64px;height:64px;border-radius:50%;background:var(--red)}
  .brand__name{font-size:30px;font-weight:600;color:var(--navy);line-height:1}

  .person{position:absolute;right:32px;top:190px;text-align:right}
  .person__name{font-size:20px;font-weight:600;color:var(--navy);line-height:1.2}
  .person__role{font-size:15px;color:var(--red);line-height:1.3}

  .divider{position:absolute;left:42px;right:32px;top:243px;height:1px;background:var(--rule)}

  .address{position:absolute;left:42px;top:281px;font-size:15px;color:var(--ink);line-height:23px}

  .contact{position:absolute;right:32px;top:254px;list-style:none;text-align:right}
  .contact li{font-size:15px;color:var(--ink);line-height:23px;display:flex;justify-content:flex-end;align-items:center;gap:8px}
  .contact svg{width:14px;height:14px;fill:var(--navy)}

  .back-brand{position:absolute;left:50%;top:168px;transform:translate(-50%,-50%);display:flex;align-items:center;gap:14px}
  .back-brand__dot{width:70px;height:70px;border-radius:50%;background:var(--red)}
  .back-brand__name{font-size:30px;font-weight:600;color:var(--white)}

  .social{position:absolute;left:105px;right:105px;top:303px;display:flex;align-items:center;gap:6px}
  .social__line{flex:1;height:1px;background:linear-gradient(90deg,transparent,var(--white))}
  .social__line--right{background:linear-gradient(90deg,var(--white),transparent)}
  .social__dot{width:22px;height:22px;border-radius:50%;border:1.5px solid var(--white)}
</style>
</head>
<body>
  <section class="card card--front">
    <div class="edge-stripe"></div>
    <div class="faint-mark" role="img" aria-label="Faint brand emblem decoration"></div>
    <div class="brand">
      <span class="brand__dot"></span>
      <span class="brand__name">Ridgeline Garlic</span>
    </div>
    <div class="person">
      <p class="person__name">DANA MARSH</p>
      <p class="person__role">CEO/FOUNDER</p>
    </div>
    <div class="divider"></div>
    <address class="address" style="font-style:normal">P.O. Box 12<br>Larkfield, CO&nbsp;&nbsp;80000</address>
    <ul class="contact">
      <li>555-014-2270
        <svg viewBox="0 0 24 24" aria-hidden="true"><path d="M6.6 10.8a15.1 15.1 0 0 0 6.6 6.6l2.2-2.2c.3-.3.7-.4 1-.2 1.1.4 2.3.6 3.6.6.6 0 1 .4 1 1V20c0 .6-.4 1-1 1A17 17 0 0 1 3 4c0-.6.4-1 1-1h3.5c.6 0 1 .4 1 1 0 1.3.2 2.5.6 3.6.1.3 0 .7-.2 1z"/></svg></li>
      <li>dana@ridgelinegarlic.com
        <svg viewBox="0 0 24 24" aria-hidden="true"><path d="M2 5h20v14H2zM3.5 6.5 12 13l8.5-6.5z" fill-rule="evenodd"/></svg></li>
      <li>www.ridgelinegarlic.com
        <svg viewBox="0 0 24 24" aria-hidden="true"><circle cx="12" cy="12" r="10"/><path d="M2 12h20M12 2c3 3 3 17 0 20M12 2c-3 3-3 17 0 20" stroke="#fff" stroke-width="1.3" fill="none"/></svg></li>
    </ul>
  </section>

  <section class="card card--back">
    <div class="back-brand">
      <span class="back-brand__dot"></span>
      <span class="back-brand__name">Ridgeline Garlic</span>
    </div>
    <div class="social">
      <span class="social__line"></span>
      <span class="social__dot"></span>
      <span class="social__dot"></span>
      <span class="social__dot"></span>
      <span class="social__dot"></span>
      <span class="social__line social__line--right"></span>
    </div>
  </section>
</body>
</html>
```